stationary deign for trucking company

im a trucking company looking for a professional set of stationary designs i deliver goods from point a to b
Updates

When submitting stationary designs I need envelope design, letterhead, cards, I’d badge etc

Industry/Entity Type

Trucking Company

Requirements
Must have
• must have letter head, business card, envelope, fax sheet, id badge, folder, thank you card, notebook, invoice sheet.
Nice to have
• nice to have them all custom made (letterhead,envelope, business card, I’d badge etc
Should not have
• must not have prepaid sign want i unique design for items

```html
<!DOCTYPE html>
<html lang="en">
<head>
<meta charset="utf-8">
<title>Harlow Freight – Business Card</title>
<link rel="stylesheet" href="https://fonts.googleapis.com/css2?family=Montserrat:wght@600&family=Roboto:wght@400;500;700&display=swap">
<style>
  :root {
    --page-bg: #e4e4e4;
    --card-white: #ffffff;
    --card-dark: #1c1d1f;
    --brand-blue: #0d56a6;
    --ink: #111111;
    --text-grey: #555555;
    --rule: #6a6a6a;
    --silver: #a3a3a3;
  }
  * { margin: 0; padding: 0; box-sizing: border-box; }
  html, body {
    width: 1125px; height: 1200px; overflow: hidden;
    background: var(--page-bg);
    font-family: "Roboto", Arial, sans-serif;
  }
  .card {
    position: absolute; left: 156px; width: 826px; height: 471px;
    box-shadow: 0 6px 18px rgba(0,0,0,0.18);
    overflow: hidden;
  }
  .card--front { top: 106px; background: var(--card-white); }
  .card--back { top: 639px; background: var(--card-dark); }

  .brand {
    position: absolute; right: 60px; top: 74px;
    display: flex; align-items: center; gap: 14px;
  }
  .brand__square { width: 22px; height: 22px; background: var(--brand-blue); }
  .brand__name {
    font-family: "Montserrat", Arial, sans-serif; font-weight: 600;
    font-size: 31px; letter-spacing: 3px; color: var(--ink); line-height: 1;
  }

  .person { position: absolute; left: 61px; top: 238px; }
  .person__name {
    font-size: 30px; font-weight: 700; color: var(--brand-blue); line-height: 1.1;
  }
  .person__title {
    font-size: 20px; font-weight: 500; color: var(--ink); margin-top: 1px; line-height: 1.2;
  }

  .divider {
    position: absolute; left: 69px; right: 60px; top: 309px;
    height: 1px; background: var(--rule);
  }

  .contacts { position: absolute; left: 59px; top: 323px; list-style: none; }
  .contacts li {
    display: flex; align-items: center; height: 27px;
    font-size: 19px; color: var(--text-grey);
  }
  .contacts svg { width: 20px; height: 20px; margin-right: 10px; fill: var(--brand-blue); }

  .address {
    position: absolute; right: 60px; top: 349px; text-align: right;
    font-size: 19px; color: var(--text-grey); line-height: 27px; font-style: normal;
  }

  .footer-band { position: absolute; left: 0; bottom: 0; width: 826px; height: 50px; }
  .website {
    position: absolute; left: 503px; bottom: 13px;
    font-size: 19px; letter-spacing: 3.4px; color: #ffffff;
  }

  .back-mark {
    position: absolute; inset: 0;
    display: flex; align-items: center; justify-content: center;
    font-family: "Montserrat", Arial, sans-serif; font-weight: 600;
    font-size: 46px; letter-spacing: 5px; color: var(--silver);
  }
</style>
</head>
<body>
  <section class="card card--front">
    <div class="brand">
      <span class="brand__square"></span>
      <span class="brand__name">HARLOW FREIGHT</span>
    </div>

    <div class="person">
      <div class="person__name">MARK ELLISON</div>
      <div class="person__title">CEO/FOUNDER</div>
    </div>

    <div class="divider"></div>

    <ul class="contacts">
      <li>
        <svg viewBox="0 0 24 24" aria-hidden="true"><path d="M6.6 10.8a15.1 15.1 0 0 0 6.6 6.6l2.2-2.2a1 1 0 0 1 1-.25 11.4 11.4 0 0 0 3.6.57 1 1 0 0 1 1 1V20a1 1 0 0 1-1 1A17 17 0 0 1 3 4a1 1 0 0 1 1-1h3.5a1 1 0 0 1 1 1c0 1.25.2 2.45.57 3.57a1 1 0 0 1-.25 1z"/></svg>
        555 210 4478
      </li>
      <li>
        <svg viewBox="0 0 24 24" aria-hidden="true"><path d="M7 1h10a2 2 0 0 1 2 2v18a2 2 0 0 1-2 2H7a2 2 0 0 1-2-2V3a2 2 0 0 1 2-2zm0 3v14h10V4zm5 15.2a1 1 0 1 0 0 2 1 1 0 0 0 0-2z"/></svg>
        555 318 2290
      </li>
      <li>
        <svg viewBox="0 0 24 24" aria-hidden="true"><path d="M2 6h20v12H2zm1.5 1.2L12 13l8.5-5.8V7h-17z"/></svg>
        mark@harlowfreight.com
      </li>
    </ul>

    <address class="address">
      1420 Birchwood Road<br>
      Anchorage, Alaska 99508
    </address>

    <svg class="footer-band" viewBox="0 0 826 50" aria-hidden="true">
      <path d="M0 20 H468 L451 37 H0 Z" fill="var(--ink)"/>
      <path d="M0 40 H450 L487 3 H826 V50 H0 Z" fill="var(--brand-blue)"/>
    </svg>
    <div class="website">www.harlowfreight.com</div>
  </section>

  <section class="card card--back">
    <div class="back-mark">HARLOW FREIGHT</div>
  </section>
</body>
</html>
```